Fresh, modern, fun business card for pediatric dental practice

Need a business card for fresh, modern, fun pediatric dental practice

Clean look that matches our website's font and colors

We prefer the look of curved corners on business cards

Target Market(s)

parents (mothers) of young children, professionals, mid-high class

Industry/Entity Type

Dental

Contact Information for Business Card

Maplebrook Pediatric Dentistry
482 Quarry Lane
Suite 517
Alder Falls, PA 17599
717.555.0193
www.maplebrookkidsdental.example

Mei-Ran Tsai, DMD
Corinne Walbeck, DMD
(we are working on our email address, but we would like that on the card as well)

Font styles to use
Sans Serif

Requirements
Must have
• All info; we would also like to make cards for individual staff members
• colors from our website and color palatte, attatched
• use same font and design as website for branding
Nice to have
• clean, simple card that has a pop of color
• we would like to see a few designs with our tag line "where smiles get brighter"
• we are not sure if we want to have it on there or not
• we would like to see a few designs incorporating the ribbon graphic on our website where the word WELCOME is

```html
<!DOCTYPE html>
<html lang="en">
<head>
<meta charset="utf-8">
<title>Maplebrook Pediatric Dentistry — Business Card</title>
<link rel="stylesheet" href="https://fonts.googleapis.com/css2?family=Open+Sans:wght@600&family=Roboto:wght@400&family=Signika:wght@600&display=swap">
<style>
  :root {
    --backdrop: #c4c4c4;
    --card: #4d2f4b;
    --gold: #e0a31b;
    --pink: #c5478a;
    --ink-light: #ece6ec;
    --divider: #8a4d78;
  }
  * { margin: 0; padding: 0; box-sizing: border-box; }
  html, body { width: 1200px; height: 576px; overflow: hidden; background: var(--backdrop); }
  .stage { position: relative; width: 1200px; height: 576px; }

  .card {
    position: absolute;
    top: 138px;
    width: 484px;
    height: 294px;
    background: var(--card);
    border-radius: 14px;
    overflow: hidden;
  }
  .card--front { left: 82px; }
  .card--back { left: 602px; }

  .brand-dot {
    position: absolute;
    border-radius: 50%;
    background: var(--gold);
  }
  .brand-name {
    position: absolute;
    font-family: "Open Sans", sans-serif;
    font-weight: 600;
    color: var(--gold);
    text-align: center;
    line-height: 1.15;
    white-space: nowrap;
  }

  /* front */
  .card--front .brand-dot { left: 219px; top: 66px; width: 50px; height: 50px; }
  .card--front .brand-name { left: 0; width: 484px; top: 138px; font-size: 28px; }
  .front-web {
    position: absolute;
    left: 0; width: 484px; top: 266px;
    text-align: center;
    font-family: "Roboto", sans-serif;
    font-size: 11.5px;
    line-height: 14px;
    letter-spacing: 0.6px;
    color: var(--ink-light);
  }
  .front-web .accent { color: var(--gold); }
  .rule-accent { position: absolute; top: 272px; width: 48px; height: 2px; }
  .rule-accent--left { left: 84px; }
  .rule-accent--right { left: 354px; }

  /* back */
  .card--back .brand-dot { left: 102px; top: 98px; width: 40px; height: 40px; }
  .card--back .brand-name { left: 4px; width: 236px; top: 152px; font-size: 18px; }
  .back-divider {
    position: absolute; left: 236px; top: 58px;
    width: 1px; height: 176px; background: var(--divider);
  }
  .contact {
    position: absolute; left: 252px; top: 0;
    font-family: "Roboto", sans-serif;
    color: var(--ink-light);
  }
  .contact__name {
    position: absolute; top: 74px; white-space: nowrap;
    font-family: "Signika", sans-serif; font-weight: 600;
    font-size: 18px; color: var(--gold);
  }
  .contact__title { position: absolute; top: 97px; font-size: 10px; white-space: nowrap; }
  .contact__address { position: absolute; top: 127px; font-size: 12.5px; line-height: 16px; white-space: nowrap; }
  .contact__lines { position: absolute; top: 168px; list-style: none; font-size: 11.5px; line-height: 16px; white-space: nowrap; }
  .contact__lines li { display: flex; align-items: center; gap: 6px; }
  .contact__lines svg { width: 9px; height: 9px; flex: none; }
  .contact__lines .accent { color: var(--pink); }
</style>
</head>
<body>
<main class="stage">
  <section class="card card--front" aria-label="Card front">
    <div class="brand-dot" aria-hidden="true"></div>
    <p class="brand-name">Maplebrook<br>Pediatric Dentistry</p>
    <svg class="rule-accent rule-accent--left" viewBox="0 0 48 2" aria-hidden="true"><polygon points="0,1 48,0 48,2" fill="var(--pink)"/></svg>
    <p class="front-web">www.<span class="accent">maplebrookkidsdental</span>.example</p>
    <svg class="rule-accent rule-accent--right" viewBox="0 0 48 2" aria-hidden="true"><polygon points="0,0 48,1 0,2" fill="var(--pink)"/></svg>
  </section>

  <section class="card card--back" aria-label="Card back">
    <div class="brand-dot" aria-hidden="true"></div>
    <p class="brand-name">Maplebrook<br>Pediatric Dentistry</p>
    <div class="back-divider" aria-hidden="true"></div>
    <div class="contact">
      <p class="contact__name">Corinne Walbeck</p>
      <p class="contact__title">DMD</p>
      <p class="contact__address">482 Quarry Lane<br>Suite 517 Alder Falls, PA 17599</p>
      <ul class="contact__lines">
        <li>
          <svg viewBox="0 0 10 10" aria-hidden="true"><path d="M1 3 Q5 0 9 3 L8 4.5 L6.5 3.8 L6.5 3 Q5 2.6 3.5 3 L3.5 3.8 L2 4.5 Z M2.5 5 H7.5 L8.5 9 H1.5 Z" fill="var(--gold)"/></svg>
          717.555.0193
        </li>
        <li>
          <svg viewBox="0 0 10 10" aria-hidden="true"><rect x="0.5" y="2" width="9" height="6.5" fill="var(--gold)"/><path d="M0.5 2 L5 5.8 L9.5 2" fill="none" stroke="var(--card)" stroke-width="0.9"/></svg>
          name@maplebrookkidsdental.example
        </li>
        <li>
          <svg viewBox="0 0 10 10" aria-hidden="true"><circle cx="5" cy="5" r="4.3" fill="none" stroke="var(--gold)" stroke-width="1.1"/><ellipse cx="5" cy="5" rx="1.8" ry="4.3" fill="none" stroke="var(--gold)" stroke-width="0.9"/><line x1="0.7" y1="5" x2="9.3" y2="5" stroke="var(--gold)" stroke-width="0.9"/></svg>
          <span>www.<span class="accent">maplebrookkidsdental</span>.example</span>
        </li>
      </ul>
    </div>
  </section>
</main>
</body>
</html>
```